Architectural, Engineering and Design Build

Tovandex4.com
Veteran Disabled Certified company is doing business in Architecture, Engineer and Design build - look simialr websites and come up with design follow following website
https://hollis-darnet.example/
https://www.venlorcogroup.example/
https://www.pembrisgc.example/contract-vehicles/service-disabled-veteran-owned-small-business-sdvosb/
https://www.corbelnetlink.example/about/sdvosb/

Target Market(s)

US - Defense and Federal Government

Industry/Entity Type

Colors
0054AA
0677BA
7BADD7
CADEEF
E8F1F8

Requirements
Must have
• Army, American patriotism , Buildings, construction, architecture, engineering
Nice to have
• I need to attract federal government agencies and Defense

```html
<!DOCTYPE html>
<html lang="en">
<head>
<meta charset="utf-8">
<title>Tovandex4 — Service Disabled Veteran Owned Small Business</title>
<link href="https://fonts.googleapis.com/css2?family=Rubik:wght@400;500;600&family=Roboto:wght@400;500;700&display=swap" rel="stylesheet">
<style>
:root{
  --navy:#121c63;
  --navy-deep:#0e1752;
  --red:#d8131b;
  --ink:#141414;
  --body:#4a4a4a;
  --white:#ffffff;
  --card-shadow:0 4px 18px rgba(0,0,0,.10);
}
*{margin:0;padding:0;box-sizing:border-box}
html,body{width:1200px;height:3585px;overflow:hidden;background:var(--white)}
body{font-family:"Roboto",sans-serif;color:var(--body);position:relative}
h1,h2,h3,.brand-name{font-family:"Rubik",sans-serif}
.abs{position:absolute}

/* header */
.site-header{position:absolute;top:0;left:0;width:1200px;height:117px;background:var(--white)}
.brand{position:absolute;left:97px;top:30px;display:flex;align-items:center;gap:10px}
.brand-mark{width:52px;height:52px;border-radius:50%;background:var(--navy)}
.brand-name{font-weight:600;font-size:26px;color:var(--navy);letter-spacing:1px}
.rfq{position:absolute;left:863px;top:24px;font-size:16px;font-weight:700;color:var(--red)}
.main-nav a{position:absolute;top:64px;font-size:17px;color:var(--ink);text-decoration:none}
.main-nav a.active{color:var(--red);font-weight:500;text-decoration:underline;text-underline-offset:4px}

/* hero */
.hero{position:absolute;top:117px;left:0;width:1200px;height:469px;
  background:linear-gradient(100deg,#2c3568 0%,#3a3d4a 30%,#2b2d33 55%,#5a2a33 80%,#b8202c 100%)}
.hero-title{position:absolute;top:225px;left:0;width:1200px;text-align:center;color:var(--white);
  font-weight:500;font-size:44px;line-height:54px}
.hero-rule{position:absolute;top:350px;left:542px;width:117px;height:4px;background:var(--red)}

/* about */
.photo-frame{position:absolute;left:117px;top:714px;width:455px;height:418px;border:2px solid var(--red)}
.about-photo{position:absolute;left:97px;top:695px;width:463px;height:421px;
  background:linear-gradient(135deg,#5d7a3a,#8f9c6a 45%,#6f6a5c 70%,#3d5a8a)}
.section-h{font-weight:500;color:var(--ink);font-size:33px;line-height:42px}
.red-rule{height:4px;background:var(--red)}
.about-text{position:absolute;left:626px;font-size:15.5px;line-height:31px;color:var(--body);width:450px}
.about-text .hl{color:var(--red)}

/* services */
.services{position:absolute;top:1233px;left:0;width:1200px;height:723px}
.services-panel{position:absolute;left:0;top:0;width:601px;height:723px;background:var(--navy)}
.services-photo{position:absolute;left:601px;top:0;width:599px;height:723px;
  background:linear-gradient(170deg,#b9b4aa 0%,#8a7f70 40%,#c98a3c 60%,#7b7368 80%,#a79d8f 100%)}
.services-title{position:absolute;left:97px;top:79px;color:var(--white);font-size:33px;font-weight:500}
.services-rule{position:absolute;left:97px;top:137px;width:92px;height:3px;background:var(--white)}
.service{position:absolute;left:0;width:601px;color:var(--white)}
.service.is-active{background:var(--white);color:var(--ink)}
.service.is-active h3{color:var(--red)}
.service.is-active p{color:var(--ink)}
.service svg{position:absolute;left:100px;top:34px;width:52px;height:52px}
.service h3{position:absolute;left:187px;top:30px;font-size:22px;font-weight:500}
.service p{position:absolute;left:187px;top:68px;font-size:14.5px;line-height:26px;width:390px}
.service-sep{position:absolute;left:0;top:534px;width:601px;height:1px;background:rgba(255,255,255,.35)}

/* testimonials */
.testimonials-title{position:absolute;top:2038px;left:0;width:1200px;text-align:center;font-size:33px;font-weight:500;color:var(--ink)}
.card{position:absolute;top:2188px;width:308px;height:185px;background:var(--white);border-radius:14px;box-shadow:var(--card-shadow)}
.card p{position:absolute;top:70px;left:22px;width:264px;text-align:center;font-size:14.5px;line-height:26px;color:var(--body)}
.avatar{position:absolute;top:2141px;width:88px;height:88px;border-radius:50%;background:linear-gradient(#c9ccd3,#8d93a0);border:3px solid var(--white)}
.avatar-badge{position:absolute;top:2201px;width:28px;height:28px;border-radius:50%;background:var(--white);box-shadow:0 1px 3px rgba(0,0,0,.25)}
.reviewer{position:absolute;top:2400px;font-size:15.5px;font-weight:500;color:var(--ink)}
.stars{position:absolute;top:2401px;color:#f2c21b;font-size:13px;letter-spacing:1px}
.slider-arrow{position:absolute;top:2265px}

/* projects */
.projects-band{position:absolute;top:2512px;left:0;width:1200px;height:335px;background:var(--red)}
.projects-title{position:absolute;top:2582px;left:0;width:1200px;text-align:center;color:var(--white);font-size:33px;font-weight:500}
.proj-btn{position:absolute;top:2584px;width:35px;height:34px;border:1.5px solid var(--white)}
.proj-btn.light{background:var(--white)}
.project{position:absolute;top:2670px;width:282px;height:333px;border:3px solid #e9e9e9;box-shadow:0 2px 8px rgba(0,0,0,.15)}
.project-label{position:absolute;top:3026px;width:282px;text-align:center;font-size:16px;font-weight:700;color:#3a3a3a}

/* footer */
.site-footer{position:absolute;top:3139px;left:0;width:1200px;height:446px;background:var(--navy)}
.footer-brand{position:absolute;left:97px;top:72px;display:flex;flex-direction:column;align-items:center;gap:10px;width:174px}
.footer-brand .brand-mark{background:var(--white);width:80px;height:80px}
.footer-brand .brand-name{color:var(--white);font-size:28px}
.social{position:absolute;top:227px;width:26px;height:26px;border-radius:50%;background:var(--white)}
.footer-h{position:absolute;top:58px;color:var(--white);font-size:21px;font-weight:500}
.quick-links a{position:absolute;left:320px;color:var(--white);font-size:15px;text-decoration:none;display:flex;align-items:center;gap:10px}
.contact-item{position:absolute;left:530px;display:flex;align-items:center;gap:14px;color:var(--white);font-size:15.5px}
.contact-icon{width:36px;height:36px;border-radius:50%;background:var(--white);display:flex;align-items:center;justify-content:center}
.newsletter-text{position:absolute;left:828px;top:117px;width:290px;color:var(--white);font-size:15px;line-height:31px}
.email-field{position:absolute;left:832px;top:186px;width:268px;color:var(--white);font-size:15px;padding-bottom:6px;border-bottom:2px solid var(--white)}
.subscribe{position:absolute;left:835px;top:241px;width:146px;height:51px;border-radius:26px;background:var(--white);color:var(--navy);font-family:"Rubik",sans-serif;font-weight:500;font-size:18px;display:flex;align-items:center;justify-content:center}
.footer-rule{position:absolute;left:97px;top:376px;width:1004px;height:1px;background:rgba(255,255,255,.6)}
.copyright{position:absolute;top:398px;left:0;width:1200px;text-align:center;color:var(--white);font-size:15px}
</style>
</head>
<body>

<header class="site-header">
  <div class="brand"><span class="brand-mark"></span><span class="brand-name">TOVANDEX4</span></div>
  <div class="rfq">Request a Quote / Submit RFQ</div>
  <nav class="main-nav">
    <a class="active" style="left:395px">Home</a>
    <a style="left:489px">About Us</a>
    <a style="left:606px">What We Do</a>
    <a style="left:746px">Industries Served</a>
    <a style="left:927px">Projects</a>
    <a style="left:1036px">Contract</a>
  </nav>
</header>

<section class="hero" role="img" aria-label="American flag draped over a dark textured stone surface">
  <h1 class="hero-title">Service Disabled Veteran Owned<br>Small Business (SDVOSB)</h1>
  <div class="hero-rule"></div>
</section>

<section class="about">
  <div class="photo-frame"></div>
  <div class="about-photo" role="img" aria-label="Soldier in uniform with his family holding an American flag in a park"></div>
  <h2 class="section-h abs" style="left:626px;top:703px">SDVOSB</h2>
  <div class="red-rule abs" style="left:627px;top:754px;width:104px"></div>
  <p class="about-text" style="top:777px">Lorem ipsum dolor sit amet, consectetur adipiscing elit, sed do eiusmod tempor incididunt ut labore et dolore magna aliqua. Ut enim nisi ut aliquip ex ea commodo consequat. Duis aute irure dolor in reprehenderit in voluptate culpa qui officia laborum.</p>
  <h2 class="section-h abs" style="left:626px;top:920px;width:520px">How Does Our SDVOSB Status Set Us Apart?</h2>
  <div class="red-rule abs" style="left:627px;top:1014px;width:104px"></div>
  <p class="about-text" style="top:1037px">Lorem ipsum dolor sit amet, consectetur adipiscing elit, sed do eiusmod tempor incididunt <span class="hl">ut labore et dolore magna</span> aliqua. Ut enim ad minim veniam, quis nisi ut aliquip ex ea consequat.</p>
</section>

<section class="services">
  <div class="services-panel">
    <h2 class="services-title">Our Services</h2>
    <div class="services-rule"></div>

    <div class="service" style="top:159px;height:132px">
      <svg viewBox="0 0 52 52" fill="none" stroke="currentColor" stroke-width="2"><rect x="10" y="8" width="32" height="40"/><path d="M6 48h40M16 14h6M30 14h6M16 22h6M30 22h6M16 30h6M30 30h6M22 48v-9h8v9"/></svg>
      <h3>Buildings</h3>
      <p>Lorem ipsum dolor sit amet, consectetur adipiscing elit, sed do eiusmod tempor incididunt magna aliqua.</p>
    </div>
    <div class="service is-active" style="top:291px;height:117px">
      <svg viewBox="0 0 52 52" fill="none" stroke="#d8131b" stroke-width="2" style="top:26px"><path d="M12 48V6M18 48V6M12 6h34M12 14l6-8M12 22l6-8M12 30l6-8M12 38l6-8M4 10h8M40 6v10M36 16h8v6h-8zM24 48V30h20v18M28 36h4M36 36h4M28 42h4M36 42h4M2 48h48"/></svg>
      <h3 style="top:18px">Construction</h3>
      <p style="top:54px">Lorem ipsum dolor sit amet, consectetur adipiscing elit, sed do eiusmod tempor incididunt magna aliqua.</p>
    </div>
    <div class="service" style="top:408px;height:126px">
      <svg viewBox="0 0 52 52" fill="none" stroke="currentColor" stroke-width="2" style="top:22px"><rect x="4" y="10" width="40" height="34"/><path d="M10 38l10-14 8 8 6-8 6 14zM30 4l16 16-12 12M42 16l4-4"/></svg>
      <h3 style="top:16px">Architecture</h3>
      <p style="top:56px">Lorem ipsum dolor sit amet, consectetur adipiscing elit, sed do eiusmod tempor incididunt magna aliqua.</p>
    </div>
    <div class="service-sep"></div>
    <div class="service" style="top:535px;height:130px">
      <svg viewBox="0 0 52 52" fill="none" stroke="currentColor" stroke-width="2" style="top:26px"><circle cx="18" cy="32" r="7"/><circle cx="18" cy="32" r="13" stroke-dasharray="5 3"/><circle cx="38" cy="14" r="4"/><circle cx="38" cy="14" r="9" stroke-dasharray="4 3"/><circle cx="42" cy="38" r="3"/><circle cx="42" cy="38" r="7" stroke-dasharray="3 3"/></svg>
      <h3 style="top:8px">Engineering Theme</h3>
      <p style="top:46px">Lorem ipsum dolor sit amet, consectetur adipiscing elit, sed do eiusmod tempor incididunt magna aliqua.</p>
    </div>
  </div>
  <div class="services-photo" role="img" aria-label="Two engineers in hard hats and safety vests reviewing plans at a building construction site"></div>
</section>

<section class="testimonials">
  <h2 class="testimonials-title">Testimonials</h2>
  <div class="red-rule abs" style="left:554px;top:2090px;width:92px"></div>

  <svg class="slider-arrow" style="left:48px" width="18" height="28" viewBox="0 0 18 28" fill="none" stroke="#141414" stroke-width="2"><path d="M14 2L4 14l10 12"/></svg>
  <svg class="slider-arrow" style="left:1150px" width="18" height="28" viewBox="0 0 18 28" fill="none" stroke="#141414" stroke-width="2"><path d="M4 2l10 12-10 12"/></svg>

  <div class="card" style="left:111px"><p>Sed ut perspiciatis unde omnis iste natus error sit voluptatem accusantium doloremque laudantium, totam rem aperiam, eaque ipsa</p></div>
  <div class="card" style="left:445px"><p>Sed ut perspiciatis unde omnis iste natus error sit voluptatem accusantium doloremque laudantium, totam rem aperiam, eaque ipsa</p></div>
  <div class="card" style="left:780px"><p>Sed ut perspiciatis unde omnis iste natus error sit voluptatem accusantium doloremque laudantium, totam rem aperiam, eaque ipsa</p></div>

  <div class="avatar" role="img" aria-label="Reviewer portrait" style="left:221px"></div>
  <div class="avatar" role="img" aria-label="Reviewer portrait" style="left:555px"></div>
  <div class="avatar" role="img" aria-label="Reviewer portrait" style="left:889px"></div>
  <div class="avatar-badge" style="left:275px"></div>
  <div class="avatar-badge" style="left:609px"></div>
  <div class="avatar-badge" style="left:943px"></div>

  <span class="reviewer" style="left:192px">Jhon Deo</span><span class="stars" style="left:279px">★★★★★</span>
  <span class="reviewer" style="left:526px">Jhon Deo</span><span class="stars" style="left:613px">★★★★★</span>
  <span class="reviewer" style="left:860px">Jhon Deo</span><span class="stars" style="left:947px">★★★★★</span>
</section>

<section class="projects">
  <div class="projects-band"></div>
  <h2 class="projects-title">Our Projects</h2>
  <div class="proj-btn" style="left:1012px"><svg width="32" height="31" viewBox="0 0 32 31" fill="none" stroke="#fff" stroke-width="2"><path d="M18 10l-5 5.5 5 5.5"/></svg></div>
  <div class="proj-btn light" style="left:1052px"><svg width="32" height="31" viewBox="0 0 32 31" fill="none" stroke="#141414" stroke-width="2"><path d="M14 10l5 5.5-5 5.5"/></svg></div>

  <div class="project" role="img" aria-label="American flag on a pole against an evening sky" style="left:15px;background:linear-gradient(160deg,#6f7d8c,#c3b49a 50%,#8a3a3a)"></div>
  <div class="project" role="img" aria-label="City skyline with high-rise towers above a park at dusk" style="left:312px;background:linear-gradient(180deg,#6c7aa8,#b58aa6 45%,#4b5f8a 70%,#4d7a3a)"></div>
  <div class="project" role="img" aria-label="Building under construction with a tower crane at sunset" style="left:608px;background:linear-gradient(180deg,#7d8fa6,#d8a860 55%,#5a4a3a)"></div>
  <div class="project" role="img" aria-label="Architect reviewing blueprints beside a laptop at a desk" style="left:903px;background:linear-gradient(160deg,#e8e6e2,#cfcac2 55%,#9a8a7a)"></div>

  <div class="project-label" style="left:15px">LOREM IPSUM DOLOR SIT</div>
  <div class="project-label" style="left:312px">LOREM IPSUM DOLOR SIT</div>
  <div class="project-label" style="left:608px">LOREM IPSUM DOLOR SIT</div>
  <div class="project-label" style="left:903px">LOREM IPSUM DOLOR SIT</div>
</section>

<footer class="site-footer">
  <div class="footer-brand"><span class="brand-mark"></span><span class="brand-name">TOVANDEX4</span></div>
  <span class="social" style="left:112px"></span>
  <span class="social" style="left:154px"></span>
  <span class="social" style="left:194px"></span>
  <span class="social" style="left:235px"></span>

  <h3 class="footer-h" style="left:320px">Quick Links</h3>
  <nav class="quick-links">
    <a style="top:98px"><svg width="14" height="12" viewBox="0 0 14 12" fill="#fff"><path d="M0 5h9V1l5 5-5 5V7H0z"/></svg>Home</a>
    <a style="top:129px"><svg width="14" height="12" viewBox="0 0 14 12" fill="#fff"><path d="M0 5h9V1l5 5-5 5V7H0z"/></svg>About Us</a>
    <a style="top:160px"><svg width="14" height="12" viewBox="0 0 14 12" fill="#fff"><path d="M0 5h9V1l5 5-5 5V7H0z"/></svg>What We Do</a>
    <a style="top:191px"><svg width="14" height="12" viewBox="0 0 14 12" fill="#fff"><path d="M0 5h9V1l5 5-5 5V7H0z"/></svg>Industries Served</a>
    <a style="top:222px"><svg width="14" height="12" viewBox="0 0 14 12" fill="#fff"><path d="M0 5h9V1l5 5-5 5V7H0z"/></svg>Projects</a>
    <a style="top:253px"><svg width="14" height="12" viewBox="0 0 14 12" fill="#fff"><path d="M0 5h9V1l5 5-5 5V7H0z"/></svg>Contract</a>
  </nav>

  <h3 class="footer-h" style="left:530px">Contact Us</h3>
  <div class="contact-item" style="top:109px"><span class="contact-icon"><svg width="14" height="18" viewBox="0 0 14 18" fill="#121c63"><path d="M7 0a7 7 0 0 0-7 7c0 5 7 11 7 11s7-6 7-11a7 7 0 0 0-7-7zm0 10a3 3 0 1 1 0-6 3 3 0 0 1 0 6z"/></svg></span>Company Name,United State.</div>
  <div class="contact-item" style="top:168px"><span class="contact-icon"><svg width="18" height="13" viewBox="0 0 18 13" fill="#121c63"><path d="M0 0h18v13H0zM1.5 1.5L9 7l7.5-5.5" stroke="#fff" stroke-width="1.3"/></svg></span>info@companyname.in</div>
  <div class="contact-item" style="top:228px"><span class="contact-icon"><svg width="16" height="16" viewBox="0 0 16 16" fill="#121c63"><path d="M3 0l3 4-2 2c1 2 4 5 6 6l2-2 4 3-2 3C7 16 0 9 0 3z"/></svg></span>+1888 8888 8888</div>

  <h3 class="footer-h" style="left:828px">Sign Up To Our Newsletter</h3>
  <p class="newsletter-text">Lorem ipsum dolor sit amet,consectetur adipiscing elit,adipiscing elit.</p>
  <div class="email-field">Email</div>
  <div class="subscribe">Subscribe</div>

  <div class="footer-rule"></div>
  <p class="copyright">Copyrights@2024.Tovandex4.All Rights Reserved</p>
</footer>

</body>
</html>
```